Industrial Project Sign

We need an eye catching (but professional) industrial project sign that will be very large (roughly 12' high x 18' wide). This sign will be highly visible from the adjacent high speed highway.

* The following needs to be at the bottom of the signage: Logo (uploaded), Name (Brightline Property Partners, Inc.) (uploaded) and phone number (415)736-2958

*Name of Project - "Meridale Commerce Park"

* Text items
Land for Sale
Build to Suit
Zoning: Industrial (G I & L I)

* Interesting background that is eye catching
Updates

Good morning all,

We are considering all designers options as we go and are waiting for the final designs to come in by the 4th so that we can give each one a good look.   If you have any new designs, questions, further design options or any tweeks you want to do to current designs, please do so at this time.

Thanks to all of you for your submissions.

Industry/Entity Type

Industrial

```html
<!DOCTYPE html>
<html lang="en">
<head>
<meta charset="utf-8">
<title>Meridale Commerce Park – Land for Sale</title>
<link rel="stylesheet" href="https://fonts.googleapis.com/css2?family=Open+Sans:wght@400;600;700;800&display=swap">
<style>
  :root {
    --maroon: #6e1216;
    --black: #0a0a0a;
    --slate: #6f6f6f;
    --grey-text: #555555;
    --white: #ffffff;
    --dot-grey: #9a9a9a;
  }
  html, body {
    margin: 0;
    padding: 0;
    width: 1200px;
    height: 800px;
    overflow: hidden;
    background: var(--white);
  }
  .sign {
    position: relative;
    width: 1200px;
    height: 800px;
    background: var(--white);
    font-family: "Open Sans", Arial, sans-serif;
    overflow: hidden;
  }
  .project-name {
    position: absolute;
    top: 14px;
    left: 0;
    width: 100%;
    margin: 0;
    text-align: center;
    font-size: 60px;
    font-weight: 700;
    letter-spacing: 1px;
    color: var(--black);
    text-transform: uppercase;
  }
  .dot-rule {
    position: absolute;
    left: 70px;
    width: 1064px;
    height: 12px;
  }
  .dot-rule--top { top: 89px; }
  .dot-rule--bottom { top: 706px; }

  .offer-band {
    position: absolute;
    top: 133px;
    left: 0;
    width: 1200px;
    height: 80px;
  }
  .offer-band svg { position: absolute; inset: 0; }
  .offer-text {
    position: absolute;
    top: 0;
    height: 80px;
    line-height: 80px;
    margin: 0;
    font-size: 56px;
    font-weight: 700;
    color: var(--white);
    text-transform: uppercase;
    white-space: nowrap;
  }
  .offer-text--sale { left: 30px; }
  .offer-text--build { left: 662px; }

  .site-photo {
    position: absolute;
    top: 213px;
    left: 0;
    width: 1200px;
    height: 219px;
    background: linear-gradient(180deg, #8d8a83 0%, #6b6a66 35%, #4d5560 60%, #7a6b5a 85%, #8a7a60 100%);
  }
  .zoning-band {
    position: absolute;
    top: 432px;
    left: 0;
    width: 1200px;
    height: 85px;
    background: var(--slate);
    color: var(--white);
    text-align: center;
    line-height: 85px;
    font-size: 56px;
    font-weight: 700;
    text-transform: uppercase;
    margin: 0;
    white-space: nowrap;
  }
  .brand-mark {
    position: absolute;
    top: 548px;
    left: 318px;
    width: 110px;
    height: 110px;
    background: var(--maroon);
  }
  .company-name {
    position: absolute;
    top: 580px;
    left: 474px;
    margin: 0;
    font-size: 27px;
    font-weight: 600;
    color: var(--grey-text);
    white-space: nowrap;
  }
  .company-rule {
    position: absolute;
    top: 619px;
    left: 470px;
    width: 450px;
    height: 4px;
    background: var(--maroon);
  }
  .company-phone {
    position: absolute;
    top: 616px;
    left: 468px;
    margin: 0;
    font-size: 60px;
    font-weight: 700;
    color: var(--black);
    white-space: nowrap;
    letter-spacing: 1px;
  }
  .website {
    position: absolute;
    top: 728px;
    left: 0;
    width: 100%;
    margin: 0;
    text-align: center;
    font-size: 46px;
    font-weight: 700;
    color: var(--slate);
    text-transform: uppercase;
    white-space: nowrap;
  }
  .website-domain { color: var(--maroon); }
</style>
</head>
<body>
<main class="sign">
  <h1 class="project-name">Meridale Commerce Park</h1>

  <svg class="dot-rule dot-rule--top" viewBox="0 0 1064 12" aria-hidden="true">
    <defs>
      <pattern id="dotsTop" width="26" height="12" patternUnits="userSpaceOnUse">
        <circle cx="5" cy="6" r="3.6" fill="var(--maroon)"/>
        <circle cx="18" cy="6" r="4.4" fill="var(--dot-grey)"/>
      </pattern>
    </defs>
    <rect width="1064" height="12" fill="url(#dotsTop)"/>
  </svg>

  <section class="offer-band">
    <svg width="1200" height="80" viewBox="0 0 1200 80" aria-hidden="true">
      <rect x="0" y="0" width="1200" height="80" fill="var(--black)"/>
      <polygon points="0,0 650,0 612,80 0,80" fill="var(--maroon)"/>
    </svg>
    <p class="offer-text offer-text--sale">Land for Sale</p>
    <p class="offer-text offer-text--build">Build to Suit</p>
  </section>

  <div class="site-photo" role="img" aria-label="Aerial photograph of an industrial plant with conveyors, brick and blue buildings and steam stacks"></div>

  <p class="zoning-band">Zoning: Industrial (G I &amp; L I)</p>

  <div class="brand-mark" aria-hidden="true"></div>
  <p class="company-name">Brightline Property Partners, Inc.</p>
  <div class="company-rule" aria-hidden="true"></div>
  <p class="company-phone">(415)736-2958</p>

  <svg class="dot-rule dot-rule--bottom" viewBox="0 0 1064 12" aria-hidden="true">
    <defs>
      <pattern id="dotsBottom" width="26" height="12" patternUnits="userSpaceOnUse">
        <circle cx="5" cy="6" r="3.6" fill="var(--maroon)"/>
        <circle cx="18" cy="6" r="4.4" fill="var(--dot-grey)"/>
      </pattern>
    </defs>
    <rect width="1064" height="12" fill="url(#dotsBottom)"/>
  </svg>

  <p class="website">www.<span class="website-domain">brightlinepartners</span>.com</p>
</main>
</body>
</html>
```